Bed Company needs business card

Hello, we are a bed company that makes specialized magnets for beds. We are an alternative healing company. I need a modern and upscale business card. Please incorporate my logo for the card.

Accepted file formats are AI, EPS, and Press-Ready PDFS.

Please include all fonts or convert them to outlines regardless of file type.

If you are designing the card in Photoshop the file Must be 1200dpi.

I am open to anything for the business card.  I really like all of your designs and if you want to change the color of the logo, you can.  I will be making the final selection by Friday.  Thank You for all of your designs.  Feel Free to submit different color logos if you want.  

Reason: I will make a decision Final on Friday April 20th. 2012. Good Luck and Thank you all for the designs.

Target Market(s)

My target Market is people, who are looking for alternative healing.

Industry/Entity Type

Business

Requirements
Must have
• My logo must be incorporated. The front card must have

Name
Job Title

Address
Work
Cell
Fax
email
web

Just put in fake info for the card.

The back of the card. I want the logo on the back with color. I just want it to look modern and cool.

```html
<!DOCTYPE html>
<html lang="en">
<head>
<meta charset="utf-8">
<title>Restwell Coil – Business Card</title>
<link rel="stylesheet" href="https://fonts.googleapis.com/css2?family=Open+Sans:wght@400;700&display=swap">
<style>
  :root {
    --backdrop-light: #dedede;
    --backdrop-dark: #adadad;
    --leaf: #52b848;
    --forest: #0e6333;
    --web-green: #0e5e2e;
    --paper: #ffffff;
    --brand: #2a8f3c;
  }
  * { margin: 0; padding: 0; box-sizing: border-box; }
  html, body { width: 1200px; height: 900px; overflow: hidden; }
  body {
    position: relative;
    font-family: "Open Sans", Arial, sans-serif;
    background: radial-gradient(ellipse at 45% 45%, var(--backdrop-light) 0%, var(--backdrop-dark) 100%);
  }
  .card {
    position: absolute;
    top: 291px;
    width: 508px;
    height: 318px;
    box-shadow: 0 1px 3px rgba(0,0,0,0.15);
  }
  .card-front { left: 75px; background: var(--leaf); color: var(--paper); }
  .card-back { left: 625px; background: var(--paper); }

  .name-band {
    position: absolute;
    left: 0; right: 0;
    top: 56px;
    height: 80px;
    background: var(--forest);
    border-top: 3px solid var(--paper);
    border-bottom: 3px solid var(--paper);
    text-align: center;
  }
  .person-name { font-size: 26px; font-weight: 400; line-height: 1; margin-top: 12px; }
  .person-title { font-size: 15px; line-height: 1; margin-top: 6px; }

  .event-address { position: absolute; left: 45px; top: 159px; font-size: 13.5px; }
  .phone-list {
    position: absolute; left: 48px; top: 193px;
    font-size: 13px; line-height: 17.5px;
    border-collapse: collapse;
  }
  .phone-list td { padding: 0; }
  .phone-list .label { width: 34px; }
  .phone-list .colon { width: 17px; }
  .email { position: absolute; left: 48px; top: 262px; font-size: 13.5px; }
  .website { position: absolute; left: 48px; top: 280px; font-size: 13.5px; color: var(--web-green); }

  .brand {
    position: absolute;
    left: 0; right: 0; top: 140px;
    display: flex; align-items: center; justify-content: center; gap: 14px;
  }
  .brand-square { width: 34px; height: 34px; background: var(--brand); }
  .brand-name { font-size: 40px; font-weight: 700; color: var(--brand); line-height: 1; }
</style>
</head>
<body>
  <section class="card card-front">
    <div class="name-band">
      <h1 class="person-name">Daniel Reyes</h1>
      <p class="person-title">director</p>
    </div>
    <p class="event-address">June 5-8, 2012, Harbor Hall East, Lakeview IL, Booth 2210</p>
    <table class="phone-list">
      <tr><td class="label">tel</td><td class="colon">:</td><td>(555) 214 367</td></tr>
      <tr><td class="label">cell</td><td class="colon">:</td><td>(555) 214 890</td></tr>
      <tr><td class="label">fax</td><td class="colon">:</td><td>(555) 214 368</td></tr>
    </table>
    <p class="email">office@restwellcoil.com</p>
    <p class="website">www.restwell-coil.com</p>
  </section>

  <section class="card card-back">
    <div class="brand">
      <span class="brand-square"></span>
      <span class="brand-name">Restwell Coil</span>
    </div>
  </section>
</body>
</html>
```